Landing page design for my current website

I need a landing page designed for my Wordpress website. My website is Velmorquay.com, and I need a page that will serve as a landing page for online ads I run. Please follow the color scheme of the current website

This web page will be targeted towards real estate owners who are looking for a property manager. Above the fold needs to have a CTA form headlined with "As a Rental Property Owner, I Want More Protection, Less Stress, and Drama-Free Living"

A few highlights that can be listed beyond the CTA and fold

- Comprehensive Property Management
Full-service management covering tenant placement, leasing, maintenance, and inspections.

Maximized Rental Income
Proven strategies to optimize rental rates and minimize vacancies, ensuring higher ROI.

Stress-Free Management
We handle all tenant interactions, maintenance requests, and property issues, so you don't have to.

Experienced Team
Over a decade of experience in managing single-family homes, small multifamily units, and apartment complexes.

Advanced Technology
Utilize cutting-edge property management software for efficient communication, rent collection, and maintenance tracking.

Tenant Screening and Placement
Thorough background checks and tenant screening processes to ensure reliable and responsible tenants.

Regular Property Inspections
Routine inspections to maintain property condition and address issues before they become costly problems.

Legal Compliance
Expertise in local and federal rental laws to keep your properties compliant and avoid legal hassles.

Transparent Reporting
Detailed monthly reports and financial statements to keep you informed about your property's performance.

Personalized Service
Tailored management plans to meet the unique needs of your properties and investment goals.
Effective Tenant Conflict Resolution
Skilled in handling challenging tenant situations, ensuring conflicts are resolved quickly and professionally to maintain a peaceful living environment and protect your investment.

```html
<!DOCTYPE html>
<html lang="en">
<head>
<meta charset="utf-8">
<title>Velmorquay Realty – Property Management</title>
<link href="https://fonts.googleapis.com/css2?family=Montserrat:wght@600;700;800&family=Lato:wght@400;500&display=swap" rel="stylesheet">
<style>
  :root {
    --navy: #12417a;
    --navy-field: #416a94;
    --white: #ffffff;
    --ink: #1b1b1b;
    --page: #ffffff;
  }
  * { box-sizing: border-box; margin: 0; padding: 0; }
  html, body { width: 823px; height: 1200px; overflow: hidden; background: var(--page); }
  body { position: relative; font-family: "Lato", sans-serif; color: var(--ink); }

  .site-header {
    position: absolute; top: 0; left: 0; width: 823px; height: 70px;
    display: flex; align-items: center; justify-content: space-between;
    padding: 0 78px 0 76px; background: var(--white);
  }
  .brand { display: flex; align-items: center; gap: 8px; }
  .brand-dot { width: 20px; height: 20px; border-radius: 50%; background: var(--navy); }
  .brand-name {
    font-family: "Montserrat", sans-serif; font-weight: 700; font-size: 18px;
    color: var(--navy); letter-spacing: 0.5px; text-transform: uppercase;
  }

  .hero {
    position: absolute; top: 70px; left: 0; width: 823px; height: 290px;
    background: linear-gradient(180deg, #3a3238 0%, #4b4648 35%, #3d3a38 70%, #5a4a3a 100%);
  }
  .hero-title {
    position: absolute; top: 64px; left: 0; width: 823px; text-align: center;
    font-family: "Montserrat", sans-serif; font-weight: 700; font-size: 23px;
    line-height: 35.5px; color: var(--white); text-transform: uppercase;
  }

  .quote-box {
    position: absolute; top: 296px; left: 66px; width: 692px; height: 129px;
    background: var(--navy); border-radius: 29px; padding-top: 22px;
  }
  .quote-title {
    text-align: center; font-family: "Montserrat", sans-serif; font-weight: 700;
    font-size: 17.5px; color: var(--white); text-transform: uppercase;
  }
  .quote-form { display: flex; gap: 10.5px; margin: 20px 0 0 27px; }
  .field {
    width: 119.5px; height: 36px; border: 1px solid #d5dde8; border-radius: 5px;
    background: var(--navy-field); color: var(--white); padding-left: 9px;
    font-family: "Montserrat", sans-serif; font-weight: 700; font-size: 8.5px;
    display: flex; align-items: center; text-transform: uppercase;
  }
  .submit {
    width: 119px; height: 36px; border-radius: 5px; background: var(--white);
    color: var(--ink); font-family: "Montserrat", sans-serif; font-weight: 700;
    font-size: 8.5px; display: flex; align-items: center; justify-content: center;
    text-transform: uppercase;
  }

  .highlights-title {
    position: absolute; top: 467px; left: 0; width: 823px; text-align: center;
    font-family: "Montserrat", sans-serif; font-weight: 800; font-size: 28px;
    color: var(--navy); text-transform: uppercase;
  }
  .highlights {
    position: absolute; top: 528px; left: 59px;
    display: grid; grid-template-columns: repeat(4, 162px);
    column-gap: 19px; row-gap: 22px;
  }
  .card {
    height: 167px; background: var(--white); border-radius: 10px;
    box-shadow: 0 4px 18px rgba(0,0,0,0.12); text-align: center; padding-top: 14px;
  }
  .card.offset-2 { grid-column: 2; margin-top: 2px; }
  .card.offset-3 { grid-column: 3; margin-top: 2px; }
  .card-icon {
    display: flex; align-items: center; justify-content: center;
    width: 54px; height: 54px; margin: 0 auto;
  }
  .card-icon::before {
    content: ""; width: 42px; height: 42px; border-radius: 50%; background: var(--navy);
  }
  .card-title {
    margin-top: 12px; font-family: "Montserrat", sans-serif; font-weight: 700;
    font-size: 8.1px; line-height: 16.5px; color: var(--navy); text-transform: uppercase;
  }
  .card-text {
    margin: 1px auto 0; width: 140px; font-size: 7.4px; line-height: 14px; color: var(--ink);
  }

  .site-footer {
    position: absolute; top: 1134px; left: 0; width: 823px; height: 66px;
    background: var(--navy); color: var(--white); display: flex;
    align-items: center; justify-content: center; font-size: 14px;
  }
</style>
</head>
<body>
  <header class="site-header">
    <div class="brand">
      <span class="brand-dot"></span>
      <span class="brand-name">Velmorquay Realty</span>
    </div>
    <svg class="menu-toggle" width="26" height="20" viewBox="0 0 26 20" aria-label="Menu">
      <rect x="0" y="0" width="24" height="2.4" rx="1.2" fill="#111"/>
      <rect x="4" y="8.6" width="22" height="2.4" rx="1.2" fill="#111"/>
      <rect x="8" y="17.4" width="18" height="2.4" rx="1.2" fill="#111"/>
    </svg>
  </header>

  <section class="hero" role="img" aria-label="Photo of a large modern farmhouse at dusk">
    <h1 class="hero-title">As a rental property owner, I want more<br>protection, less stress, and<br>drama-free living</h1>
  </section>

  <section class="quote-box">
    <h2 class="quote-title">Get a free quote</h2>
    <div class="quote-form">
      <div class="field">Name</div>
      <div class="field">Email</div>
      <div class="field">Phone</div>
      <div class="field">Rental</div>
      <div class="submit">Submit</div>
    </div>
  </section>

  <h2 class="highlights-title">Our highlights</h2>

  <main class="highlights">
    <article class="card">
      <div class="card-icon" role="img" aria-label="Property management icon"></div>
      <h3 class="card-title">Comprehensive property<br>management</h3>
      <p class="card-text">Full-service management covering tenant placement, leasing, maintenance, and inspections.</p>
    </article>
    <article class="card">
      <div class="card-icon" role="img" aria-label="Rental income icon"></div>
      <h3 class="card-title">Maximized rental<br>income</h3>
      <p class="card-text">Proven strategies to optimize rental rates and minimize vacancies, ensuring higher ROI.</p>
    </article>
    <article class="card">
      <div class="card-icon" role="img" aria-label="Stress-free management icon"></div>
      <h3 class="card-title">Stress-free<br>management</h3>
      <p class="card-text">We handle all tenant interactions, maintenance requests, and property issues, so you don't have to.</p>
    </article>
    <article class="card">
      <div class="card-icon" role="img" aria-label="Stress-free management icon"></div>
      <h3 class="card-title">Stress-free<br>management</h3>
      <p class="card-text">We handle all tenant interactions, maintenance requests, and property issues, so you don't have to.</p>
    </article>
    <article class="card">
      <div class="card-icon" role="img" aria-label="Property management icon"></div>
      <h3 class="card-title">Comprehensive property<br>management</h3>
      <p class="card-text">Full-service management covering tenant placement, leasing, maintenance, and inspections.</p>
    </article>
    <article class="card">
      <div class="card-icon" role="img" aria-label="Rental income icon"></div>
      <h3 class="card-title">Maximized rental<br>income</h3>
      <p class="card-text">Proven strategies to optimize rental rates and minimize vacancies, ensuring higher ROI.</p>
    </article>
    <article class="card">
      <div class="card-icon" role="img" aria-label="Property inspections icon"></div>
      <h3 class="card-title">Regular property<br>inspections</h3>
      <p class="card-text">We handle all tenant interactions, maintenance requests, and property issues, so you don't have to.</p>
    </article>
    <article class="card">
      <div class="card-icon" role="img" aria-label="Legal compliance icon"></div>
      <h3 class="card-title">Legal<br>compliance</h3>
      <p class="card-text">We handle all tenant interactions, maintenance requests, and property issues, so you don't have to.</p>
    </article>
    <article class="card offset-2">
      <div class="card-icon" role="img" aria-label="Reporting icon"></div>
      <h3 class="card-title">Transparent<br>reporting</h3>
      <p class="card-text">We handle all tenant interactions, maintenance requests, and property issues, so you don't have to.</p>
    </article>
    <article class="card offset-3">
      <div class="card-icon" role="img" aria-label="Personalized service icon"></div>
      <h3 class="card-title">Personalized<br>service</h3>
      <p class="card-text">We handle all tenant interactions, maintenance requests, and property issues, so you don't have to.</p>
    </article>
  </main>

  <footer class="site-footer">Copyrights@2024.Velmorquay Realty.All Rights Reserved</footer>
</body>
</html>
```